Technical Communications firm needs an article turned into a white paper

We want to redesign a 3-part blog series into a white paper that we can print for a conference. I've consolidated the three posts into the attached Word document.

We are looking for a light, easy to read design. Good use of graphics to support the message. I've added the graphics we used in the original post.

You can view them at
http://www.brightquillpages.com/blog/are-you-satisfied-with-your-dita-solution/

Target Market(s)

Product managers from High-tech, Finance, and Medical industries.

Industry/Entity Type

Information Technology

Colors

Designer to choose colors to be used in the design.

Requirements
Must have
• Must be modern, light, easy to read and slick design. Try to incorporate the graphics provided, but feel free to add more. Must retain the lists and tables.
• Must align with our website/brand.
• Must be easy to read. So not too busy.
• Please move all footnotes to endnotes. You'll need to rework the numbering.
Nice to have
• Awesome coverpage.
Should not have
• Hokey clipart. Not too heavy or hard to read.

```html
<!DOCTYPE html>
<html lang="en">
<head>
<meta charset="utf-8">
<title>Technology – White Paper Page 7</title>
<link href="https://fonts.googleapis.com/css2?family=Carlito:wght@400;700&display=swap" rel="stylesheet">
<style>
  :root {
    --navy: #1c1a8f;
    --sky: #19a9e1;
    --ink: #2a2a2a;
    --rule: #9fd3ec;
    --paper: #ffffff;
    --cloud-light: #e6e8ea;
    --cloud-mid: #b9bdc1;
    --cloud-dark: #8d9196;
  }
  * { margin: 0; padding: 0; box-sizing: border-box; }
  html, body {
    width: 927px; height: 1200px; overflow: hidden;
    background: var(--paper);
  }
  .page {
    position: relative; width: 927px; height: 1200px;
    font-family: "Carlito", "Calibri", sans-serif;
    color: var(--ink);
  }
  .spine {
    position: absolute; left: 110px; top: 110px;
    width: 3px; height: 950px; background: var(--navy);
  }
  .brand {
    position: absolute; left: 84px; top: 58px;
    display: flex; align-items: center; gap: 14px;
  }
  .brand-mark {
    width: 84px; height: 84px; border-radius: 50%;
    background: var(--navy);
  }
  .brand-name {
    font-weight: 700; font-size: 27px; line-height: 1.0;
    color: var(--navy); letter-spacing: 0.5px;
  }
  .page-tag {
    position: absolute; left: 744px; top: 70px; width: 126px; height: 28px;
    border-top: 1px solid var(--rule); border-bottom: 1px solid var(--rule);
    text-align: center; line-height: 26px;
    font-weight: 700; font-size: 15.5px; color: var(--navy); letter-spacing: 1px;
  }
  .section-title {
    position: absolute; left: 180px; top: 148px; width: 692px;
    text-align: center; font-weight: 700; font-size: 50px; color: var(--navy);
    line-height: 1.2;
  }
  .section-title span { text-decoration: underline; text-decoration-thickness: 3px; text-underline-offset: 5px; }
  .hero {
    position: absolute; left: 180px; top: 226px; width: 691px; height: 290px;
    background: linear-gradient(180deg, var(--cloud-mid) 0%, var(--cloud-light) 45%, var(--cloud-mid) 85%, var(--cloud-dark) 100%);
  }
  .intro {
    position: absolute; left: 172px; top: 534px; width: 696px;
    font-size: 14.6px; line-height: 18.4px;
  }
  .intro .lead { text-align: center; padding: 0 4px; }
  .intro .follow { text-indent: 28px; margin-top: 3px; line-height: 22px; }
  .subhead {
    position: absolute; left: 172px; top: 680px; width: 696px;
    text-align: center; font-weight: 700; font-size: 34px; color: var(--navy);
  }
  .subhead span { text-decoration: underline; text-decoration-thickness: 2px; text-underline-offset: 4px; }
  .body {
    position: absolute; left: 172px; top: 734px; width: 696px;
    font-size: 14.6px; line-height: 22.4px;
  }
  .issues { list-style: none; margin: 4px 0 8px 108px; }
  .issues li { position: relative; padding-left: 1px; text-align: justify; }
  .issues li::before {
    content: ""; position: absolute; left: -24px; top: 9px;
    width: 5px; height: 5px; border-radius: 50%; background: var(--ink);
  }
  .body .indent { text-indent: 30px; text-align: justify; }
  .footer-dots {
    position: absolute; left: 104px; top: 1071px;
  }
</style>
</head>
<body>
<div class="page">
  <div class="spine"></div>

  <div class="brand">
    <div class="brand-mark"></div>
    <div class="brand-name">BRIGHTQUILL<br>PAGES</div>
  </div>

  <div class="page-tag">PAGE 7</div>

  <h1 class="section-title">2) <span>Technology</span></h1>

  <div class="hero" role="img" aria-label="Red hot-air balloon straining to lift a heavy iron anchor against a grey cloudy sky"></div>

  <div class="intro">
    <p class="lead">This article is part of a series based on the results of a survey of more than 250 technical communication professionals conducted by The Markup Herald in 2017 entitled The DITA Satisfaction Survey<sup>4</sup>. In the survey, almost two-thirds of respondents voiced some concerns with their DITA deployment.</p>
    <p class="follow">In my previous article, I examined some of the principal issues related to skills development. This article looks at how technology affects DITA Satisfaction.</p>
  </div>

  <h2 class="subhead"><span>Issues Related to Technology</span></h2>

  <div class="body">
    <p>The second highest ranked reported issues fall under the category of technology. These include</p>
    <ul class="issues">
      <li>Our technology doesn’t meet our expectations. Ranked 4th by 62% of respondents</li>
      <li>Our publishing capabilities are limited. Ranked 5th by 60% of respondents, and</li>
      <li>We have challenges with content localization. Ranked 10th by 35% of respondents.</li>
      <li>We often hear about the failure of the technology as it relates to performance or complexity. While technology may seem the most likely culprit, it is often not the root cause of the problem.</li>
    </ul>
    <p class="indent">The good news is that you have invested in an open standard and your systems likely make it possible to lift your content—and much of your metadata—out of your existing system and put it</p>
  </div>

  <svg class="footer-dots" width="770" height="16" viewBox="0 0 770 16" aria-hidden="true">
    <g>
      <circle cx="8" cy="8" r="6.5" fill="var(--navy)"/><circle cx="31" cy="8" r="6.5" fill="var(--sky)"/>
      <circle cx="54" cy="8" r="6.5" fill="var(--navy)"/><circle cx="77" cy="8" r="6.5" fill="var(--sky)"/>
      <circle cx="100" cy="8" r="6.5" fill="var(--navy)"/><circle cx="123" cy="8" r="6.5" fill="var(--sky)"/>
      <circle cx="146" cy="8" r="6.5" fill="var(--navy)"/><circle cx="169" cy="8" r="6.5" fill="var(--sky)"/>
      <circle cx="192" cy="8" r="6.5" fill="var(--navy)"/><circle cx="215" cy="8" r="6.5" fill="var(--sky)"/>
      <circle cx="238" cy="8" r="6.5" fill="var(--navy)"/><circle cx="261" cy="8" r="6.5" fill="var(--sky)"/>
      <circle cx="284" cy="8" r="6.5" fill="var(--navy)"/><circle cx="307" cy="8" r="6.5" fill="var(--sky)"/>
      <circle cx="330" cy="8" r="6.5" fill="var(--navy)"/><circle cx="353" cy="8" r="6.5" fill="var(--sky)"/>
      <circle cx="376" cy="8" r="6.5" fill="var(--navy)"/><circle cx="399" cy="8" r="6.5" fill="var(--sky)"/>
      <circle cx="422" cy="8" r="6.5" fill="var(--navy)"/><circle cx="445" cy="8" r="6.5" fill="var(--sky)"/>
      <circle cx="468" cy="8" r="6.5" fill="var(--navy)"/><circle cx="491" cy="8" r="6.5" fill="var(--sky)"/>
      <circle cx="514" cy="8" r="6.5" fill="var(--navy)"/><circle cx="537" cy="8" r="6.5" fill="var(--sky)"/>
      <circle cx="560" cy="8" r="6.5" fill="var(--navy)"/><circle cx="583" cy="8" r="6.5" fill="var(--sky)"/>
      <circle cx="606" cy="8" r="6.5" fill="var(--navy)"/><circle cx="629" cy="8" r="6.5" fill="var(--sky)"/>
      <circle cx="652" cy="8" r="6.5" fill="var(--navy)"/><circle cx="675" cy="8" r="6.5" fill="var(--sky)"/>
      <circle cx="698" cy="8" r="6.5" fill="var(--navy)"/><circle cx="721" cy="8" r="6.5" fill="var(--sky)"/>
      <circle cx="744" cy="8" r="6.5" fill="var(--navy)"/><circle cx="762" cy="8" r="6.5" fill="var(--sky)"/>
    </g>
  </svg>
</div>
</body>
</html>
```